Coastline Premier Retreats Business Card Design

Design a business card for Coastline Premier Retreats. Look at the website for colors and reference. Card should have logo, name, title, office number, mobile number, email, URL and a tagline like, "Luxury Hotel & Resort Email Marketing" (This might change).

https://www.coastlinepremierretreats.example

The rest I will leave up to your imagination.

Contact Information for Business Card

Logo, name, title, office number, mobile number, email, URL and a tagline like, "Luxury Hotel & Resort Email Marketing" (This might change).

```html
<!DOCTYPE html>
<html lang="en">
<head>
<meta charset="utf-8">
<title>Coastline Premier Retreats Business Card</title>
<link rel="stylesheet" href="https://fonts.googleapis.com/css2?family=Montserrat:wght@400;500;600;700;800&display=swap">
<style>
  :root {
    --orange: #f47321;
    --ink: #141414;
    --text: #1e1e1e;
    --card: #fafbfc;
    --backdrop: #e4e2e3;
  }
  * { box-sizing: border-box; margin: 0; padding: 0; }
  html, body { width: 1200px; height: 1108px; overflow: hidden; }
  body {
    background: var(--backdrop);
    font-family: "Montserrat", sans-serif;
    color: var(--text);
    position: relative;
  }
  .card {
    position: absolute;
    width: 729px;
    height: 437px;
    background: var(--card);
    overflow: hidden;
  }
  .card--front { left: 237px; top: 67px; }
  .card--back { left: 244px; top: 580px; }
  .card-band { position: absolute; left: 0; bottom: 0; width: 729px; height: 14px; }

  .brand-name {
    display: flex;
    align-items: center;
    gap: 10px;
    font-weight: 800;
    color: var(--ink);
    letter-spacing: 0.01em;
    white-space: nowrap;
  }
  .brand-mark { background: var(--orange); flex: none; }

  .card--front .brand-name {
    position: absolute;
    left: 26px;
    top: 208px;
    font-size: 18px;
  }
  .card--front .brand-mark { width: 13px; height: 13px; }

  .contact-block {
    position: absolute;
    left: 348px;
    top: 98px;
    width: 367px;
    height: 232px;
    border-left: 2px solid var(--orange);
    padding-left: 16px;
  }
  .person-name { font-size: 26px; font-weight: 700; color: var(--orange); line-height: 1.1; }
  .person-title { font-size: 16px; font-weight: 500; margin-top: 1px; }
  .address { font-size: 16px; line-height: 22px; margin-top: 26px; }
  .contact-list { list-style: none; margin-top: 15px; }
  .contact-list li {
    display: flex;
    align-items: center;
    gap: 10px;
    font-size: 14.5px;
    letter-spacing: -0.01em;
    height: 25px;
    white-space: nowrap;
  }
  .contact-list svg { width: 15px; height: 15px; flex: none; fill: var(--orange); }

  .card--back .brand-name {
    position: absolute;
    left: 0;
    right: 0;
    top: 166px;
    justify-content: center;
    font-size: 40px;
    gap: 16px;
  }
  .card--back .brand-mark { width: 28px; height: 28px; }
  .tagline {
    position: absolute;
    left: 0; right: 0;
    top: 373px;
    text-align: center;
    font-size: 18px;
    font-weight: 600;
    color: var(--ink);
  }
  .tagline .accent { color: var(--orange); }
</style>
</head>
<body>

<section class="card card--front" aria-label="Business card front">
  <div class="brand-name"><span class="brand-mark"></span>Coastline Premier Retreats</div>

  <div class="contact-block">
    <h1 class="person-name">Rania Soufan</h1>
    <p class="person-title">Owner</p>
    <p class="address">418 Harbor Row, Suite 210<br>Port Ellis, OR 97031</p>
    <ul class="contact-list">
      <li>
        <svg viewBox="0 0 16 16" aria-hidden="true"><path d="M1 6c0-2 3-3.5 7-3.5S15 4 15 6v1.5h-3.5V6c-1-.5-2-.6-3.5-.6S5.5 5.5 4.5 6v1.5H1z M3.5 9h9l1.5 5H2z"/></svg>
        <span>555.214.0387 x 118</span>
      </li>
      <li>
        <svg viewBox="0 0 16 16" aria-hidden="true"><path d="M4.5 0h7A1.5 1.5 0 0 1 13 1.5v13A1.5 1.5 0 0 1 11.5 16h-7A1.5 1.5 0 0 1 3 14.5v-13A1.5 1.5 0 0 1 4.5 0zM4.5 2v10.5h7V2zM8 13.3a.9.9 0 1 0 0 1.8.9.9 0 0 0 0-1.8z"/></svg>
        <span>555.630.4192</span>
      </li>
      <li>
        <svg viewBox="0 0 16 16" aria-hidden="true"><path d="M0 3h16v1.2L8 9 0 4.2z M0 5.8l8 4.8 8-4.8V13H0z"/></svg>
        <span>info@coastlinepremierretreats.example</span>
      </li>
      <li>
        <svg viewBox="0 0 16 16" aria-hidden="true"><circle cx="8" cy="8" r="7.5"/><path d="M4 3.5c1.5.5 2 1.5 1.5 2.5S7 8 6.5 9.5 5 11 5 13M10 2.5c-.5 1.5.5 2.5 2 2.5s1.5 2 .5 3-1 2.5 0 3.5" stroke="#fff" stroke-width="1.2" fill="none"/></svg>
        <span>www.coastlinepremierretreats.example</span>
      </li>
    </ul>
  </div>

  <svg class="card-band" viewBox="0 0 729 14" preserveAspectRatio="none" aria-hidden="true">
    <polygon points="0,0 390,0 377,14 0,14" fill="var(--orange)"/>
    <polygon points="398,0 729,0 729,14 385,14" fill="var(--ink)"/>
  </svg>
</section>

<section class="card card--back" aria-label="Business card back">
  <div class="brand-name"><span class="brand-mark"></span>Coastline Premier Retreats</div>
  <p class="tagline"><span class="accent">Luxury Hotel &amp; Resort</span> Email Marketing</p>
  <svg class="card-band" viewBox="0 0 729 14" preserveAspectRatio="none" aria-hidden="true">
    <polygon points="0,0 390,0 377,14 0,14" fill="var(--orange)"/>
    <polygon points="398,0 729,0 729,14 385,14" fill="var(--ink)"/>
  </svg>
</section>

</body>
</html>
```